Brochure design for International Beauty Trade Show

I neee a tri-fold company products' brochure to distribute to customers at an international trade show coming soon. We have 4 main product categories- hair and skincare, facial care, Body and bath and massage oil.
The brochure needs to include at least 2 photos of the main products of each category, benefits, call to action and our company contact info ( website and phone number).

Target Market(s)

Educated and high income earners looking for all-natural,pure, 100 organic products for their beauty and personal care needs. Our products cross all racial groups/demographics and suitable for all skin types

Industry/Entity Type

Hair And Beauty

Font styles to use
Serif

Colors

Designer to choose colors to be used in the design.

Requirements
Must have
• The design must stand out as pure and luxury and at the same time be inclusive using our logo design colors- orange and blue. Also, the content must be easy to read and captivating.
• Finally if using women pictures, please include Black, white, Asian and Latina to reflect the fact that our products are suitable for all skin types.
Nice to have
• Design the brochure such that it could be printed as a poster-banner ad.
Should not have
• Cookie cutter designs are not welcome

```html
<!DOCTYPE html>
<html lang="en">
<head>
<meta charset="utf-8">
<title>Verdane Solutions – Tri-fold Brochure</title>
<link rel="stylesheet" href="https://fonts.googleapis.com/css2?family=Cinzel:wght@500;700&family=Open+Sans:wght@400;600;700&display=swap">
<style>
  :root {
    --backdrop: #e4e4e4;
    --paper: #ffffff;
    --paper-shade: #f1f1f1;
    --orange: #f07a1a;
    --blue: #2a9be0;
    --green-deep: #1f5a14;
    --green-mid: #3f8a22;
    --green-light: #8cc63f;
    --yellow: #f5d31c;
    --ink: #3a3a3a;
    --white: #ffffff;
  }
  * { box-sizing: border-box; margin: 0; padding: 0; }
  html, body { width: 1200px; height: 1000px; overflow: hidden; }
  body {
    background: var(--backdrop);
    font-family: "Open Sans", Arial, sans-serif;
    color: var(--ink);
    position: relative;
  }
  .brochure {
    position: absolute;
    left: 60px;
    width: 1080px;
    height: 455px;
    display: flex;
    background: var(--paper);
    box-shadow: 0 8px 24px rgba(0,0,0,.18);
  }
  .brochure--outside { top: 22px; }
  .brochure--inside { top: 522px; }
  .panel {
    position: relative;
    width: 360px;
    height: 100%;
    overflow: hidden;
    background: linear-gradient(90deg, var(--paper) 70%, var(--paper-shade));
  }
  .panel + .panel { border-left: 1px solid #e6e6e6; }
  .panel__photo {
    position: absolute;
    left: 0; top: 0;
    width: 360px;
  }
  .panel__body { position: absolute; left: 0; right: 0; }
  .heading {
    font-family: "Cinzel", Georgia, serif;
    font-weight: 700;
    font-size: 24px;
    line-height: 1.05;
    letter-spacing: .5px;
  }
  .heading--blue { color: var(--blue); }
  .heading--orange { color: var(--orange); }
  .heading--yellow { color: var(--yellow); }
  .heading--white { color: var(--white); }
  .benefits { list-style: none; font-size: 12px; line-height: 1.7; margin-top: 10px; }
  .benefits li::before { content: "•"; margin-right: 7px; }
  .benefits--light { color: var(--white); }
  .checklist { list-style: none; font-size: 12px; line-height: 1.75; margin-top: 10px; }
  .checklist li { display: flex; align-items: center; gap: 8px; }
  .checklist svg { flex: none; }
  .about { position: absolute; left: 36px; top: 30px; right: 40px; color: var(--white); }
  .about p { font-size: 12.5px; line-height: 1.45; margin-top: 10px; }
  .contact { text-align: center; font-size: 15px; line-height: 1.55; }
  .brand-name {
    font-family: "Open Sans", Arial, sans-serif;
    font-weight: 700;
    color: var(--orange);
    font-size: 24px;
    letter-spacing: 1px;
    display: flex; align-items: center; justify-content: center; gap: 10px;
    margin-bottom: 16px;
  }
  .brand-dot { width: 22px; height: 22px; border-radius: 50%; background: var(--blue); }
  .brand-mark { width: 92px; height: 92px; border-radius: 50%; background: var(--orange); margin: 0 auto; }
  .tagline {
    position: absolute; left: 40px; top: 42px; right: 24px;
    color: var(--white); font-size: 25px; line-height: 1.2;
  }
  .tagline strong { font-weight: 700; display: block; }
  .web-link { color: var(--blue); font-weight: 600; font-size: 15px; text-align: center; }
  .product-shot { position: absolute; }
</style>
</head>
<body>

<section class="brochure brochure--outside">
  <article class="panel panel--hair">
    <svg class="panel__photo" width="360" height="250" viewBox="0 0 360 250" role="img" aria-label="Woman with long dark hair beside bottles of hair and skin oil">
      <defs>
        <linearGradient id="hairPhoto" x1="0" y1="0" x2="1" y2="1">
          <stop offset="0" stop-color="#f4f1ee"/><stop offset=".5" stop-color="#c9957a"/><stop offset="1" stop-color="#8a5a2e"/>
        </linearGradient>
      </defs>
      <path d="M0 0H360V180Q200 215 0 200Z" fill="url(#hairPhoto)"/>
      <path d="M0 205Q200 222 360 186" fill="none" stroke="var(--orange)" stroke-width="5"/>
    </svg>
    <div class="panel__body" style="top:232px; left:60px;">
      <h2 class="heading heading--blue">Hair &amp;<br>Skincare</h2>
      <ul class="benefits">
        <li>Natural moisturizer</li>
        <li>Heal damaged hair or sensitive scalp</li>
        <li>Soften curly and frizzy hair</li>
        <li>Anti-aging, remove wrinkles</li>
        <li>Reduce sebum secretion</li>
        <li>Tone, sooth and restore luster</li>
        <li>Restore fair complexion</li>
      </ul>
    </div>
  </article>

  <article class="panel panel--about">
    <svg class="panel__photo" width="360" height="260" viewBox="0 0 360 260" role="img" aria-label="Bamboo stalks and black spa stones on a green background">
      <defs>
        <linearGradient id="aboutPhoto" x1="0" y1="0" x2="0" y2="1">
          <stop offset="0" stop-color="var(--green-deep)"/><stop offset=".55" stop-color="var(--green-mid)"/><stop offset="1" stop-color="#2b2b2b"/>
        </linearGradient>
      </defs>
      <path d="M0 0H360V215Q180 170 0 230Z" fill="url(#aboutPhoto)"/>
      <path d="M0 233Q180 172 360 218" fill="none" stroke="var(--orange)" stroke-width="5"/>
    </svg>
    <div class="about">
      <h2 class="heading heading--white" style="font-size:21px;">About Us</h2>
      <p>Verdane Solutions is an export/import company. Our mission is to satisfy our customers by supplying them with pure, 100% organic products, that make them more attractive and solve the most common skin and hair problems.</p>
    </div>
    <div class="panel__body contact" style="top:290px;">
      <div class="brand-name"><span class="brand-dot"></span>VERDANE</div>
      <div>(800) 555-0147</div>
      <div>hello@verdane.com</div>
      <div>www.verdane.com</div>
    </div>
  </article>

  <article class="panel panel--cover">
    <svg class="panel__photo" width="360" height="290" viewBox="0 0 360 290" role="img" aria-label="Spa stones, purple orchid, lit candle and bamboo leaves on green">
      <defs>
        <linearGradient id="coverPhoto" x1="0" y1="0" x2="1" y2="1">
          <stop offset="0" stop-color="var(--green-mid)"/><stop offset=".6" stop-color="var(--green-light)"/><stop offset="1" stop-color="#3a3a2a"/>
        </linearGradient>
      </defs>
      <path d="M0 0H360V285Q180 245 0 220Z" fill="url(#coverPhoto)"/>
      <path d="M0 223Q180 248 360 288" fill="none" stroke="var(--orange)" stroke-width="5"/>
    </svg>
    <div class="tagline"><strong>Natural Solutions</strong>to Forever Beauty</div>
    <div class="panel__body" style="top:312px;">
      <div class="brand-mark" aria-label="Verdane Solutions"></div>
      <div class="web-link" style="margin-top:20px;">www.verdane.com</div>
    </div>
  </article>
</section>

<section class="brochure brochure--inside">
  <article class="panel panel--facial">
    <svg class="panel__photo" width="360" height="190" viewBox="0 0 360 190" role="img" aria-label="Woman applying facial cream against a green background">
      <defs>
        <linearGradient id="facialPhoto" x1="0" y1="0" x2="1" y2="1">
          <stop offset="0" stop-color="var(--green-light)"/><stop offset=".5" stop-color="#7a4e35"/><stop offset="1" stop-color="var(--green-mid)"/>
        </linearGradient>
      </defs>
      <path d="M0 0H360V160Q180 150 0 180Z" fill="url(#facialPhoto)"/>
      <path d="M0 182Q180 152 360 163" fill="none" stroke="var(--orange)" stroke-width="5"/>
    </svg>
    <div class="panel__body" style="top:198px; left:40px;">
      <h2 class="heading heading--orange">Facial Care</h2>
      <ul class="benefits">
        <li>Reduce sebum secretion</li>
        <li>Eliminate toxins &amp; blemishes</li>
        <li>Tighten pores</li>
        <li>Dries pimples</li>
        <li>Remove blackheads</li>
      </ul>
    </div>
    <svg class="product-shot" style="left:70px; top:360px;" width="230" height="80" role="img" aria-label="Jar of facial cream and boxed facial soap">
      <rect width="230" height="80" rx="8" fill="#e7ece2"/>
    </svg>
  </article>

  <article class="panel panel--body">
    <svg class="panel__photo" width="360" height="215" viewBox="0 0 360 215" role="img" aria-label="Soft green bokeh background">
      <defs>
        <linearGradient id="bodyPhoto" x1="0" y1="0" x2="1" y2="1">
          <stop offset="0" stop-color="var(--green-mid)"/><stop offset="1" stop-color="var(--green-deep)"/>
        </linearGradient>
      </defs>
      <path d="M0 0H360V180Q180 172 0 205Z" fill="url(#bodyPhoto)"/>
      <path d="M0 207Q180 174 360 182" fill="none" stroke="var(--orange)" stroke-width="5"/>
    </svg>
    <div class="panel__body" style="top:22px; left:40px;">
      <h2 class="heading heading--yellow" style="font-size:21px;">Body<br>&amp; Bath Care</h2>
      <ul class="benefits benefits--light" style="font-size:11px; line-height:1.6; margin-top:8px;">
        <li>Purify and disinfect</li>
        <li>Fight acne</li>
        <li>Rejuvenate &amp; hydrate</li>
        <li>Promote healthy looking skin</li>
        <li>Remove dead cells</li>
      </ul>
    </div>
    <svg class="product-shot" style="left:70px; top:212px;" width="230" height="58" role="img" aria-label="Boxed body soaps with lemons and prickly pear fruit">
      <rect width="230" height="58" rx="8" fill="#d7e2a4"/>
    </svg>
    <svg class="product-shot" style="left:90px; top:282px;" width="250" height="173" role="img" aria-label="Woman wrapped in a white towel seated with knees drawn up">
      <rect width="250" height="173" rx="10" fill="#efe4da"/>
    </svg>
  </article>

  <article class="panel panel--massage">
    <svg class="panel__photo" width="360" height="125" viewBox="0 0 360 125" role="img" aria-label="Green bamboo leaves on a soft green background">
      <defs>
        <linearGradient id="massagePhoto" x1="0" y1="0" x2="1" y2="1">
          <stop offset="0" stop-color="var(--green-mid)"/><stop offset=".6" stop-color="var(--green-light)"/><stop offset="1" stop-color="var(--green-deep)"/>
        </linearGradient>
      </defs>
      <path d="M0 0H360V95Q180 95 0 120Z" fill="url(#massagePhoto)"/>
      <path d="M0 122Q180 97 360 97" fill="none" stroke="var(--orange)" stroke-width="5"/>
    </svg>
    <div class="panel__body" style="top:140px; left:30px;">
      <h2 class="heading heading--orange">Massage Care</h2>
      <ul class="checklist">
        <li><svg width="12" height="12" viewBox="0 0 12 12"><rect x=".75" y=".75" width="10.5" height="10.5" fill="none" stroke="var(--orange)" stroke-width="1.5"/><path d="M2.5 6l2.5 2.5L10 2" fill="none" stroke="var(--orange)" stroke-width="1.8"/></svg>Relief stress and pain</li>
        <li><svg width="12" height="12" viewBox="0 0 12 12"><rect x=".75" y=".75" width="10.5" height="10.5" fill="none" stroke="var(--orange)" stroke-width="1.5"/><path d="M2.5 6l2.5 2.5L10 2" fill="none" stroke="var(--orange)" stroke-width="1.8"/></svg>Fight muscle contraction/tenderness</li>
        <li><svg width="12" height="12" viewBox="0 0 12 12"><rect x=".75" y=".75" width="10.5" height="10.5" fill="none" stroke="var(--orange)" stroke-width="1.5"/><path d="M2.5 6l2.5 2.5L10 2" fill="none" stroke="var(--orange)" stroke-width="1.8"/></svg>Eliminate stretch marks</li>
        <li><svg width="12" height="12" viewBox="0 0 12 12"><rect x=".75" y=".75" width="10.5" height="10.5" fill="none" stroke="var(--orange)" stroke-width="1.5"/><path d="M2.5 6l2.5 2.5L10 2" fill="none" stroke="var(--orange)" stroke-width="1.8"/></svg>Pure, undiluted</li>
      </ul>
    </div>
    <svg class="product-shot" style="left:215px; top:280px;" width="115" height="150" role="img" aria-label="Bottle of massage oil with red berries">
      <rect width="115" height="150" rx="8" fill="#d9c8cc"/>
    </svg>
  </article>
</section>

</body>
</html>
```